Full 10+ Page Online Learning eBook Design - NOT just the cover :)

We currently have an eBook within the online learning space which is geared towards a consumer audience (hobbyists, interests), but we have a new 2.0 version which is geared towards professionals (certifications, training, continuing ed, career-oriented). We need a new design and need the words/copy put into the eBook, but want to keep the look and feel of the original (open to variations in design). File is attached, along with various logo options.

Target Market(s)

Professionals

Industry/Entity Type

Learning

Font styles to use
Sans Serif

Colors
33a6d7
acd036
919191

Requirements
Must have
• Must follow a very similar look a feel of the original file. We use a lot of fonts like Raleway, Gotham, Helvetica Neue, Gil Sans, DIN - anything modern looking. We also use a lot of grayish hexagons in our corporate design. Feel free to check out brightlanternhub.example to get a better sense.
Nice to have
• Include some professionally oriented icons / photos
Should not have
• No cartoonish graphics or imagery

```html
<!DOCTYPE html>
<html lang="en">
<head>
<meta charset="utf-8">
<title>Understanding the Market Opportunity</title>
<link rel="stylesheet" href="https://fonts.googleapis.com/css2?family=Questrial&display=swap">
<style>
  :root {
    --band-grey: #8f8f8f;
    --rule-grey: #919191;
    --ink: #1a1a1a;
    --paper: #ffffff;
    --city-dark: #1e1e20;
    --city-mid: #55565a;
    --city-sky: #d6d6d6;
    --city-glow: #c98a3e;
    --hex-blue: #33a6d7;
  }
  * { margin: 0; padding: 0; box-sizing: border-box; }
  html, body { width: 852px; height: 1200px; overflow: hidden; background: var(--paper); }
  .page {
    position: relative;
    width: 852px;
    height: 1200px;
    background: var(--paper);
    font-family: "Questrial", "Century Gothic", sans-serif;
    color: var(--ink);
    overflow: hidden;
  }
  .band { position: absolute; left: 0; width: 852px; height: 18px; background: var(--band-grey); }
  .band--top { top: 0; }
  .band--bottom { bottom: 0; }
  .hero-photo {
    position: absolute;
    top: 18px; left: 0;
    width: 852px; height: 484px;
    background:
      radial-gradient(ellipse 120px 260px at 42% 78%, rgba(201,138,62,0.45), transparent 70%),
      radial-gradient(ellipse 90px 180px at 12% 62%, rgba(201,138,62,0.35), transparent 70%),
      linear-gradient(180deg, var(--city-sky) 0%, #b5b5b5 14%, var(--city-mid) 32%, #34353a 60%, var(--city-dark) 100%);
  }
  .hex-field {
    position: absolute;
    right: 0; bottom: 18px;
    width: 420px; height: 320px;
    background: radial-gradient(ellipse 380px 300px at 100% 100%, rgba(51,166,215,0.16), rgba(51,166,215,0.05) 60%, transparent 80%);
  }
  .content {
    position: absolute;
    top: 524px; left: 6px;
    width: 842px;
  }
  .section-title {
    font-weight: 400;
    font-size: 21px;
    letter-spacing: 0.2px;
    text-transform: uppercase;
    line-height: 28px;
    padding-bottom: 6px;
    border-bottom: 3px solid var(--rule-grey);
    width: 672px;
    margin-bottom: 16px;
  }
  .body-copy p {
    font-size: 15.4px;
    line-height: 16.9px;
    margin-bottom: 17px;
  }
</style>
</head>
<body>
<div class="page">
  <div class="band band--top"></div>
  <div class="hero-photo" role="img" aria-label="Aerial night view of a dense city skyline with glowing orange streets and a river in the distance"></div>
  <div class="hex-field" role="img" aria-label="Faint pale blue hexagon pattern"></div>

  <main class="content">
    <h1 class="section-title">Understanding the Market Opportunity</h1>
    <div class="body-copy">
      <p>Professional training and certification has become big business in the United States. A report from Workforce Skills magazine estimated that U.S. training expenditures dramatically increased from 2014 to 2015, "soaring 14.2 percent to<br>$70.6 billion." As a subset of that, spending on outside products and services over that same period grew from<br>$6.1 billion to $8 billion, "skyrocketing" 29 percent.A survey of continuing education and training professionals found that 52 percent expected increases in their business for the current year. Those same respondents anticipated dramatic growth especially in their online and mobile businesses between now and the year 2020.</p>
      <p>Concurrently, alternative educational credentials are coming to the forefront, driven by job changers seeking new careers; increased employer acceptance of microcredentials and digital badges; the growth of learning through massive<br>open, online courses (MOOCs); and a generational mindset that embraces the notion of life-long learning. A 2014 study on alternative educational credentials by the National Statistics Office found that 51 million people had received professional certification and 21 million had earned educational certificates. All of them needed some form of training to attain their credentials.</p>
      <p>Layered on top of those stats is solid market growth fueled by technology. As a 2016 Northfield Capital Advisors report noted, "Modern technologies continue to alter the way training is delivered and processed by organizations as online, asynchronous, and mobile delivery methodologies gain more traction."</p>
      <p>The overall professional training and education market encompasses numerous sub-markets, among them the self-starter seeking professional advancement; organizationstraining workers for compliance; and companiesseeking ways to train their customers as well as their "extended enterprises" -- distributors, retailers and others that sell and service their products.</p>
      <p>What ties them all together is that they're seeking training like the kind you can offer them, and they're willing to pay for your expertise. You just need to figure out how to reach them and deliver your learning content in a scalable way while still catering to their unique needs.</p>
    </div>
  </main>

  <div class="band band--bottom"></div>
</div>
</body>
</html>
```